RVT Business Card Design

We are an independent auto dealer who specializes in commercial & fleet vehicles, we are family owned and operated and have been in business since 2001. We stock late model, low mileage, white trucks & vans. We mostly deal with companies in the construction and service industries. We are just looking to try to freshen up our old business card, we do not want to change the logo at this point, because it is well know within the southwest region & construction community. I have attached our logo and a PDF of our current business card for reference.
Updates
If the address is stacked there is no comma (,) after NE. Everyone keeps putting it in with this format and it is not correct.
482 Morrow Ave NE
Albuquerque, NM 87107
If the address is all on one line, then there will be a comma (,) after NE
482 Morrow Ave NE, Albuquerque, NM 87107
Please make changes accordingly, thank you for your attention in this matter.
Industry/Entity Type
Construction
Contact Information for Business Card
482 Morrow Ave NE, Albuquerque, NM 87107, Dorian Pellew, Vice President, dorian@rvtfleetcars.example, www.RVTfleetcars.example, ph 505-218-4470, fax 505-627-1904, cell 505-763-2085
Look and feel

```html
<!DOCTYPE html>
<html lang="en">
<head>
<meta charset="utf-8">
<title>RVT Auto Sales — Business Card</title>
<link rel="stylesheet" href="https://fonts.googleapis.com/css2?family=Open+Sans:ital,wght@0,400;0,600;1,400&family=Libre+Baskerville&display=swap">
<style>
  :root {
    --backdrop: #e8e4de;
    --card-white: #ffffff;
    --card-black: #231f20;
    --ink: #1d1d1d;
    --accent-red: #d7262b;
    --slogan-ink: #f2f2f2;
  }
  * { box-sizing: border-box; margin: 0; padding: 0; }
  html, body {
    width: 1200px;
    height: 1023px;
    overflow: hidden;
    background: var(--backdrop);
  }
  .sheet {
    width: 1200px;
    height: 1023px;
    display: flex;
    align-items: center;
    justify-content: center;
    gap: 44px;
  }
  .card {
    width: 530px;
    height: 303px;
    position: relative;
    box-shadow: 0 2px 10px rgba(0,0,0,0.18);
  }
  .card-back {
    background: var(--card-black);
    display: flex;
    align-items: center;
    justify-content: center;
  }
  .slogan {
    font-family: "Libre Baskerville", serif;
    color: var(--slogan-ink);
    font-size: 21px;
    letter-spacing: 0.5px;
    text-transform: uppercase;
  }
  .card-front {
    background: var(--card-white);
    font-family: "Open Sans", sans-serif;
    color: var(--ink);
    padding: 26px 28px;
  }
  .person-name {
    color: var(--accent-red);
    font-size: 20px;
    font-weight: 400;
    line-height: 1.15;
  }
  .person-title {
    font-size: 15px;
    line-height: 1.3;
  }
  .address {
    margin-top: 14px;
    font-size: 15px;
    line-height: 1.35;
  }
  .contact-list {
    list-style: none;
    margin-top: 18px;
    font-size: 14.5px;
    line-height: 1.32;
    width: 250px;
  }
  .contact-list li {
    display: flex;
    align-items: center;
    gap: 8px;
    white-space: nowrap;
  }
  .contact-icon {
    width: 13px;
    height: 13px;
    flex: none;
  }
  .brand {
    position: absolute;
    right: 26px;
    bottom: 22px;
    width: 200px;
    text-align: right;
  }
  .brand-name {
    font-size: 24px;
    font-weight: 600;
    color: var(--ink);
    line-height: 1;
    letter-spacing: 0.3px;
    white-space: nowrap;
  }
  .brand-tagline {
    margin-top: 8px;
    font-size: 10.5px;
    font-style: italic;
    line-height: 1.3;
  }
</style>
</head>
<body>
<main class="sheet">
  <section class="card card-back" aria-label="Card back">
    <p class="slogan">You want it… We stock it!</p>
  </section>

  <section class="card card-front" aria-label="Card front">
    <h1 class="person-name">Dorian Pellew</h1>
    <p class="person-title">Vice President</p>
    <p class="address">482 Morrow Ave NE<br>Albuquerque, NM 87107</p>
    <ul class="contact-list">
      <li>
        <svg class="contact-icon" viewBox="0 0 16 16" aria-hidden="true"><path fill="var(--accent-red)" d="M3.5 1l2.5 3-1.5 2c1 2 3 4 5 5l2-1.5 3 2.5-1.5 2.5C7 15 1 9 1 2.5z"/></svg>
        505-218-4470
      </li>
      <li>
        <svg class="contact-icon" viewBox="0 0 16 16" aria-hidden="true"><rect x="4" y="1" width="8" height="14" rx="1.5" fill="none" stroke="var(--accent-red)" stroke-width="1.6"/><circle cx="8" cy="12.5" r="0.9" fill="var(--accent-red)"/></svg>
        505-763-2085
      </li>
      <li>
        <svg class="contact-icon" viewBox="0 0 16 16" aria-hidden="true"><rect x="4" y="1" width="8" height="5" fill="var(--accent-red)"/><rect x="1" y="6" width="14" height="7" rx="1" fill="var(--accent-red)"/><rect x="4" y="11" width="8" height="4" fill="var(--card-white)" stroke="var(--accent-red)" stroke-width="1.2"/></svg>
        505-627-1904
      </li>
      <li>
        <svg class="contact-icon" viewBox="0 0 16 16" aria-hidden="true"><rect x="1" y="3" width="14" height="10" fill="var(--accent-red)"/><path d="M1.5 3.5L8 9l6.5-5.5" fill="none" stroke="var(--card-white)" stroke-width="1.3"/></svg>
        dorian@rvtfleetcars.example
      </li>
      <li>
        <svg class="contact-icon" viewBox="0 0 16 16" aria-hidden="true"><circle cx="8" cy="8" r="6.5" fill="none" stroke="var(--accent-red)" stroke-width="1.6"/><path d="M1.5 8h13M8 1.5c-3 3.5-3 9.5 0 13M8 1.5c3 3.5 3 9.5 0 13" fill="none" stroke="var(--accent-red)" stroke-width="1.1"/></svg>
        www.RVTfleetcars.example
      </li>
    </ul>

    <div class="brand">
      <p class="brand-name">RVT AUTO SALES</p>
      <p class="brand-tagline">Specializing in Commercial<br>&amp; Fleet Vehicles</p>
    </div>
  </section>
</main>
</body>
</html>
```